New Business Card Design for Manufacturing

We are an engineering/manufacturing company that offers Advanced machining/assembly/engineering services, as well as innovative products for the heavy duty engine cooling markets.

We are looking to get a new business card designed that is clean and modern looking, but still fits the wide range of technical/skilled work we do.

- We hope to use this design as the base for other design work in new Presentations, web, and print work.

Industry/Entity Type

Engineering

Contact Information for Business Card

Our preferred color of blue is (RGB) 22/71/159 but can vary slightly from that color. Our content will be our Logo and full company name (Vantrell Forge Works, Inc.), company address, name, job title, phone number with extension, cell number, fax number, website, and email address on the cards.
We'd like the full company name next to the logo, but we are open to other interpretations of that layout.
Preferably, we would like the back side to be clean with just our logo, and the front to contain all of the contact information.

Colors
2f74b4
0355a3
85abd2

Requirements
Must have
• - Logo, company name, needed content - We are open to interpretation beyond that.
• - Standard size business card.
• - Horizontal orientation.
• - Enough space for lengthy names / job titles (for example, a job title could read "Directory of Human Resources" or "V.P. of Governmental Affairs"). We need this to look clean, whether the title be short (CEO) or long (as described above).

```html
<!DOCTYPE html>
<html lang="en">
<head>
<meta charset="utf-8">
<title>Vantrell Forge Works – Business Card</title>
<link rel="stylesheet" href="https://fonts.googleapis.com/css2?family=Open+Sans:wght@400;600;700;800&display=swap">
<style>
  :root {
    --stage: #2c2c2e;
    --card: #1f1f21;
    --card-edge: #161617;
    --blue: #0a6fc4;
    --blue-deep: #16479f;
    --blue-light: #2f8fdc;
    --silver: #8e949b;
    --white: #f4f6f8;
    --muted-logo: #2a2a2d;
  }
  * { box-sizing: border-box; margin: 0; padding: 0; }
  html, body {
    width: 799px; height: 1200px; overflow: hidden;
    background: var(--stage);
    font-family: "Open Sans", Arial, sans-serif;
  }
  .stage {
    position: relative; width: 799px; height: 1200px;
    display: flex; flex-direction: column; align-items: center;
    justify-content: center; gap: 90px;
  }
  .card {
    position: relative; width: 640px; height: 366px;
    background: var(--card);
    border: 1px solid var(--card-edge);
    box-shadow: 0 18px 40px rgba(0,0,0,.45);
    overflow: hidden;
  }

  /* back side */
  .card-back { display: flex; align-items: center; justify-content: center; }
  .brand-mark {
    display: flex; align-items: center; gap: 16px;
    font-weight: 800; font-size: 64px; letter-spacing: 2px;
    color: var(--muted-logo); text-transform: uppercase;
  }
  .brand-mark .dot { width: 22px; height: 22px; background: currentColor; }

  /* front side */
  .wave { position: absolute; inset: 0; width: 100%; height: 100%; }
  .contact {
    position: absolute; left: 34px; top: 30px; color: var(--white);
  }
  .person-name { font-size: 25px; font-weight: 600; color: var(--blue-light); line-height: 1.1; }
  .person-title { font-size: 13px; margin-top: 2px; }
  .company-name { font-size: 15px; font-weight: 600; color: var(--blue-light); margin-top: 22px; }
  .details { list-style: none; margin-top: 8px; font-size: 14px; line-height: 1.45; }
  .details li { display: flex; align-items: center; gap: 9px; }
  .details svg { width: 12px; height: 12px; fill: var(--blue-light); flex: none; }
  .details .accent { color: var(--blue-light); }
  .card-front .brand-mark {
    position: absolute; right: 40px; top: 118px;
    font-size: 46px; gap: 12px; color: var(--blue);
  }
  .card-front .brand-mark .dot { width: 16px; height: 16px; }
  .address {
    position: absolute; right: 34px; bottom: 26px;
    color: var(--white); font-size: 16px; text-align: right; line-height: 1.35;
  }
</style>
</head>
<body>
<main class="stage">

  <section class="card card-back" aria-label="Card back">
    <div class="brand-mark"><span class="dot"></span>Vantrell</div>
  </section>

  <section class="card card-front" aria-label="Card front">
    <svg class="wave" viewBox="0 0 640 366" preserveAspectRatio="none" aria-hidden="true">
      <defs>
        <linearGradient id="blueBand" x1="0" y1="0" x2="1" y2="1">
          <stop offset="0" stop-color="#1d86d8"/>
          <stop offset="1" stop-color="#0d5fb3"/>
        </linearGradient>
      </defs>
      <path d="M0 215 C60 250 140 262 260 262 C400 262 520 250 640 262 L640 366 L0 366 Z" fill="#8e949b"/>
      <path d="M0 232 C70 268 150 276 270 276 C410 276 520 268 640 280 L640 366 L0 366 Z" fill="#1f1f21"/>
      <path d="M0 248 C80 286 160 290 280 290 C420 290 530 282 640 296 L640 366 L0 366 Z" fill="url(#blueBand)"/>
    </svg>

    <div class="contact">
      <p class="person-name">Elena Marsh Cole</p>
      <p class="person-title">Managing Director</p>
      <p class="company-name">Vantrell Forge Works, Inc.</p>
      <ul class="details">
        <li><svg viewBox="0 0 24 24"><path d="M6.6 10.8a15 15 0 0 0 6.6 6.6l2.2-2.2c.3-.3.7-.4 1-.2 1.1.4 2.3.6 3.6.6.6 0 1 .4 1 1V20c0 .6-.4 1-1 1A17 17 0 0 1 3 4c0-.6.4-1 1-1h3.5c.6 0 1 .4 1 1 0 1.3.2 2.5.6 3.6.1.3 0 .7-.2 1z"/></svg>555-0142-2210 (VFW)</li>
        <li><svg viewBox="0 0 24 24"><rect x="6" y="2" width="12" height="20" rx="2"/></svg>555-0178-3341</li>
        <li><svg viewBox="0 0 24 24"><path d="M6 3h12v5H6zM3 9h18v9h-3v3H6v-3H3z"/></svg>555-0193-4482</li>
        <li><svg viewBox="0 0 24 24"><path d="M2 5h20v14H2z M2 5l10 8 10-8"/></svg>emcole@vantrellforge.com</li>
        <li><svg viewBox="0 0 24 24"><circle cx="12" cy="12" r="10"/></svg>www.<span class="accent">vantrellforge</span>.com</li>
      </ul>
    </div>

    <div class="brand-mark"><span class="dot"></span>Vantrell</div>

    <p class="address">418 Millbrook Rd., Dalton<br>Falls, OH 44210</p>
  </section>

</main>
</body>
</html>
```